Varnex Consulting Business card design.

See our website www.varnexconsulting.example which will give you a good idea of what we are about. The font is called 'Play'.

I'd like a standout business card in keeping with the themes and branding on the website

Target Market(s)

professionals. HR directors

Industry/Entity Type

Business

Contact Information for Business Card

Varnex Consulting PO Box 3172 Merrowdale NSW 2291 1300 485 193 Gavin Threlkeld Principal email: career@varnexconsulting.example ABN: 71203948865

Font styles to use
Other font styles liked:
• Play

Requirements
Must have
• Must have same design colours and branding as website.
• On back I'd prefer a list of the things we do which appears below the name at the header on the website

```html
<!DOCTYPE html>
<html lang="en">
<head>
<meta charset="utf-8">
<title>Varnex Consulting – Business Card</title>
<link href="https://fonts.googleapis.com/css2?family=Play:wght@400;700&display=swap" rel="stylesheet">
<style>
  :root {
    --navy: #13263b;
    --blue: #2b93df;
    --ink: #1c2430;
    --paper: #ffffff;
    --backdrop: #a8a5a5;
  }
  * { margin: 0; padding: 0; box-sizing: border-box; }
  html, body { width: 1200px; height: 1200px; overflow: hidden; }
  body {
    background: var(--backdrop);
    font-family: "Play", sans-serif;
    color: var(--ink);
    position: relative;
  }
  .card {
    position: absolute;
    left: 240px;
    width: 720px;
    height: 420px;
    background: var(--paper);
    overflow: hidden;
  }
  .card--front { top: 120px; }
  .card--back { top: 640px; }

  .wordmark {
    position: absolute;
    font-weight: 400;
    font-size: 54px;
    line-height: 1;
    color: var(--navy);
    letter-spacing: 0.5px;
    white-space: nowrap;
  }
  .services {
    position: absolute;
    font-size: 15.5px;
    letter-spacing: 2.2px;
    color: var(--blue);
    white-space: nowrap;
  }
  .services .sep { color: var(--navy); margin: 0 4px; letter-spacing: 0; }

  /* front */
  .card--front .wordmark { left: 0; right: 0; top: 130px; text-align: center; }
  .card--front .services { left: 0; right: 0; top: 195px; text-align: center; }
  .front-web {
    position: absolute;
    left: 0; right: 0; top: 346px;
    display: flex; justify-content: center; align-items: center; gap: 14px;
    font-size: 18.5px;
    color: var(--ink);
  }
  .front-web .rule { width: 36px; height: 2px; background: var(--blue); border-radius: 2px; }
  .front-web .accent { color: var(--blue); }

  /* back */
  .header-band {
    position: absolute; left: 0; top: 0; width: 720px; height: 120px;
    background: var(--navy);
    border-bottom: 6px solid var(--blue);
  }
  .holder {
    position: absolute; right: 34px; top: 34px; text-align: right; color: #fff;
  }
  .holder-name { font-weight: 700; font-size: 25px; line-height: 1.1; }
  .holder-title { font-size: 17px; margin-top: 8px; }
  .contacts { position: absolute; left: 48px; top: 148px; font-size: 18.5px; }
  .contact-row { display: flex; align-items: center; height: 24px; }
  .contact-row svg { width: 16px; height: 14px; margin-right: 20px; flex: none; }
  .contact-row .accent { color: var(--blue); }
  .address { margin-top: 4px; height: 30px; display: flex; align-items: center; }
  .abn { margin-top: 8px; }
  .abn .label { color: var(--blue); }
  .card--back .wordmark { left: 48px; top: 314px; }
  .card--back .services { left: 48px; top: 372px; }
</style>
</head>
<body>

<section class="card card--front">
  <div class="wordmark">VARNEX CONSULTING</div>
  <div class="services">Search &amp; Select<span class="sep">|</span>Career<span class="sep">|</span>Coaching<span class="sep">|</span>Leadership<span class="sep">|</span>Outplacement</div>
  <div class="front-web">
    <span class="rule"></span>
    <span>www.<span class="accent">varnexconsulting</span>.example</span>
    <span class="rule"></span>
  </div>
</section>

<section class="card card--back">
  <div class="header-band"></div>

  <div class="holder">
    <div class="holder-name">Gavin Threlkeld</div>
    <div class="holder-title">Principal</div>
  </div>

  <div class="contacts">
    <div class="contact-row">
      <svg viewBox="0 0 16 14"><path d="M1,5 C3,1 13,1 15,5 L12,6 L11,4 H5 L4,6 Z" fill="var(--blue)"/><rect x="3" y="7" width="10" height="6" rx="1" fill="var(--blue)"/></svg>
      <span>1300 485 193</span>
    </div>
    <div class="contact-row">
      <svg viewBox="0 0 16 14"><circle cx="8" cy="7" r="6" fill="none" stroke="var(--blue)" stroke-width="1.6"/><ellipse cx="8" cy="7" rx="2.5" ry="6" fill="none" stroke="var(--blue)" stroke-width="1.2"/><line x1="2" y1="7" x2="14" y2="7" stroke="var(--blue)" stroke-width="1.2"/></svg>
      <span>www.<span class="accent">varnexconsulting</span>.example</span>
    </div>
    <div class="contact-row">
      <svg viewBox="0 0 16 14"><rect x="1" y="2" width="14" height="10" fill="var(--blue)"/><path d="M1,2 L8,8 L15,2" fill="none" stroke="#fff" stroke-width="1.4"/></svg>
      <span>career@varnexconsulting.example</span>
    </div>
    <div class="address">PO Box 3172 Merrowdale NSW 2291</div>
    <div class="abn"><span class="label">ABN:</span> 71203948865</div>
  </div>

  <div class="wordmark">VARNEX CONSULTING</div>
  <div class="services">Search &amp; Select<span class="sep">|</span>Career<span class="sep">|</span>Coaching<span class="sep">|</span>Leadership<span class="sep">|</span>Outplacement</div>
</section>

</body>
</html>
```